A5 Flyer for Financial Services Business

I am after a re-design of our business flyer to fit in with our new branding style and logo colour scheme. Wanting something with a bit of designer flair that I could not create myself. I have included the flyer which I created which lacks style so dazzle me.

I want to use the same content.

Text for main body of flyer is

Are you a small business owner, tradie or TRPQ Service Provider struggling to stay on top of your bookkeeping and compliance obligations? If so we would love to help you get back on track and take control of your business finances so that you can make informed business decisions and focus on what you do best.

We have over 20 years industry experience and, as a small business ourselves, we are able to offer our clients a personal bookkeeping solution tailored to meet the needs of your business.

Accounts Payable | Accounts Receivable
Customer Invoicing
Bank and Credit Card Reconciliations
Payroll | Superannuation | Payroll Tax
Business Activity | Instalment Activity Statements
Regular Financial Reports
Vantly and Brimfolk Set-Up and Training

```html
<!DOCTYPE html>
<html lang="en">
<head>
<meta charset="utf-8">
<title>Even Keel Financial Services – Bookkeeping Flyer</title>
<link href="https://fonts.googleapis.com/css2?family=Bebas+Neue&family=Oswald:wght@200&family=Poppins:wght@300;400;500;600;700&display=swap" rel="stylesheet">
<style>
  :root{
    --teal:#13898d;
    --teal-light:#1aa3a6;
    --navy:#0f4661;
    --charcoal:#474a4d;
    --ink:#2f3337;
    --black:#16191b;
    --paper:#ffffff;
    --mist:#eef1f3;
  }
  *{margin:0;padding:0;box-sizing:border-box}
  html,body{width:931px;height:1200px;overflow:hidden;background:var(--paper)}
  body{font-family:'Poppins',sans-serif;color:var(--ink)}
  .flyer{position:relative;width:931px;height:1200px;overflow:hidden;background:var(--paper)}
  .abs{position:absolute}
  ul{list-style:none}

  .backdrop{left:0;top:0;width:931px;height:1200px}

  .brand{left:70px;top:54px;display:flex;align-items:center;gap:14px}
  .brand-mark{width:44px;height:44px;background:var(--navy)}
  .brand-name{font-weight:300;font-size:34px;line-height:1;color:var(--teal);letter-spacing:.5px}
  .brand-sub{font-weight:300;font-size:17px;letter-spacing:7px;color:var(--teal);margin-top:4px}

  .headline{left:60px;top:192px;color:var(--paper);font-weight:400}
  .hl-big{font-family:'Bebas Neue',sans-serif;font-size:98px;line-height:.86;letter-spacing:.5px}
  .hl-bar{display:block;width:446px;background:var(--black);font-weight:700;font-size:34px;line-height:48px;padding-left:18px;margin:6px 0 10px;letter-spacing:.5px;clip-path:polygon(0 0,100% 0,94% 100%,0 100%)}
  .hl-thin{font-family:'Oswald',sans-serif;font-weight:200;font-size:84px;line-height:.9;letter-spacing:-1px}

  .hex{position:absolute;width:216px;height:114px;clip-path:polygon(20% 0,80% 0,100% 50%,80% 100%,20% 100%,0 50%);display:flex;align-items:center;padding-left:38px;gap:12px;color:var(--paper);font-size:13px;font-weight:500;line-height:1.2}
  .hex.navy{background:var(--navy)}
  .hex.grey{background:var(--charcoal)}
  .hex svg{flex:none;width:32px;height:32px}

  .badges{left:289px;top:934px;display:flex;gap:8px;align-items:center}
  .badge-shield{width:46px;height:52px;background:#d9e6d4;clip-path:polygon(0 0,100% 0,100% 70%,50% 100%,0 70%)}
  .badge-round{width:44px;height:44px;border-radius:50%;background:#1ab4e0}
  .badge-round.dark{background:var(--teal)}

  .experience{left:68px;top:1012px;width:130px;color:var(--charcoal)}
  .exp-over{font-size:14px;line-height:18px;color:var(--teal);letter-spacing:.3px}
  .exp-num{font-family:'Bebas Neue',sans-serif;font-size:96px;line-height:.8;color:var(--teal);margin-top:4px}
  .exp-num span{color:var(--charcoal)}
  .exp-tag{position:absolute;left:84px;top:46px;background:var(--teal);color:#fff;font-size:10px;padding:1px 8px;transform:rotate(-14deg)}
  .exp-ind{font-weight:700;font-size:20px;line-height:1;margin-top:4px}
  .exp-exp{font-size:11px;line-height:14px;letter-spacing:4px}

  .about{left:218px;top:1012px;width:245px;font-size:13px;line-height:1.2;color:var(--black)}

  .question{left:518px;top:718px;width:380px;font-weight:600;font-size:23px;line-height:1.27;color:var(--charcoal)}
  .question em{font-style:normal;color:var(--teal)}
  .pitch{left:520px;top:904px;width:340px;border-left:3px solid var(--navy);padding-left:14px;font-size:15px;line-height:1.27;color:var(--black)}
  .call{left:518px;top:1026px}
  .call-label{font-size:25px;font-weight:500;color:var(--teal);line-height:1}
  .call-number{display:flex;align-items:center;gap:6px;font-size:43px;font-weight:700;color:var(--black);line-height:1.2}
  .call-number svg{width:38px;height:38px}

  .web{right:73px;top:1141px;font-size:21px;font-weight:500;color:var(--paper);letter-spacing:1px;line-height:28px}
</style>
</head>
<body>
<main class="flyer">

  <svg class="abs backdrop" viewBox="0 0 931 1200" aria-hidden="true">
    <defs>
      <linearGradient id="panelFill" x1="0" y1="0" x2=".4" y2="1">
        <stop offset="0" stop-color="#1aa3a6"/>
        <stop offset=".55" stop-color="#13898d"/>
        <stop offset="1" stop-color="#0f4661"/>
      </linearGradient>
      <linearGradient id="lowerFill" x1="0" y1="0" x2="0" y2="1">
        <stop offset="0" stop-color="#ffffff"/>
        <stop offset="1" stop-color="#eef1f3"/>
      </linearGradient>
    </defs>
    <rect x="0" y="0" width="931" height="1200" fill="url(#lowerFill)"/>
    <polygon points="0,140 470,140 600,330 600,560 0,560" fill="#e3e7ea"/>
    <polygon points="0,158 478,158 590,328 560,575 0,575" fill="url(#panelFill)"/>
    <polygon points="170,1200 233,1128 931,1128 931,1200" fill="#13898d"/>
    <polygon points="0,1177 190,1177 170,1200 0,1200" fill="#0f4661"/>
  </svg>

  <svg class="abs" style="left:0;top:0" width="931" height="680" viewBox="0 0 931 680" role="img" aria-label="Photo of a person working on a laptop showing financial charts at a desk">
    <defs>
      <linearGradient id="photoFill" x1="0" y1="0" x2="1" y2="1">
        <stop offset="0" stop-color="#4d5257"/>
        <stop offset=".35" stop-color="#d9dde0"/>
        <stop offset=".7" stop-color="#c4c8cb"/>
        <stop offset="1" stop-color="#8d8f90"/>
      </linearGradient>
    </defs>
    <polygon points="615,0 931,0 931,675 395,675 395,430 520,330 545,200" fill="url(#photoFill)"/>
  </svg>

  <div class="abs brand">
    <div class="brand-mark"></div>
    <div>
      <div class="brand-name">EVEN KEEL</div>
      <div class="brand-sub">Financial Services</div>
    </div>
  </div>

  <h1 class="abs headline">
    <div class="hl-big">BOOKKEEPING</div>
    <div class="hl-bar">TAILORED TO YOUR</div>
    <div class="hl-thin">BUSINESS</div>
    <div class="hl-big">NEEDS</div>
  </h1>

  <ul class="services">
    <li class="hex grey" style="left:60px;top:524px">
      <svg viewBox="0 0 32 32" fill="none" stroke="#fff" stroke-width="2"><rect x="4" y="5" width="16" height="20"/><path d="M8 10h8M8 15h8M8 20h4"/><circle cx="23" cy="23" r="6" fill="#474a4d"/></svg>
      <span>Accounts<br>Payable<br>&amp; Accounts<br>Receivable</span>
    </li>
    <li class="hex navy" style="left:231px;top:584px">
      <svg viewBox="0 0 32 32" fill="none" stroke="#fff" stroke-width="2"><rect x="7" y="4" width="18" height="24"/><path d="M12 10h8M12 22h8"/><path d="M16 12v8"/></svg>
      <span>Customer<br>Invoicing</span>
    </li>
    <li class="hex navy" style="left:60px;top:641px">
      <svg viewBox="0 0 32 32" fill="none" stroke="#fff" stroke-width="2"><rect x="3" y="9" width="26" height="16" rx="2"/><path d="M3 14h26M7 21h6"/></svg>
      <span>Bank and<br>Credit Card<br>Reconciliations</span>
    </li>
    <li class="hex grey" style="left:231px;top:698px">
      <svg viewBox="0 0 32 32" fill="none" stroke="#fff" stroke-width="2"><circle cx="18" cy="9" r="6"/><path d="M3 20h6l6 4h10M3 27h22"/></svg>
      <span>Payroll<br>Superannuation<br>Payroll Tax</span>
    </li>
    <li class="hex grey" style="left:60px;top:756px">
      <svg viewBox="0 0 32 32" fill="none" stroke="#fff" stroke-width="2"><rect x="7" y="3" width="16" height="26" rx="2"/><circle cx="15" cy="13" r="4"/><path d="M11 23h8"/></svg>
      <span>Business<br>Activity<br>Instalment<br>Activity<br>Statements</span>
    </li>
    <li class="hex navy" style="left:231px;top:813px">
      <svg viewBox="0 0 32 32" fill="none" stroke="#fff" stroke-width="2"><ellipse cx="12" cy="10" rx="8" ry="3"/><path d="M4 10v10c0 2 4 3 8 3M4 15c0 2 4 3 8 3"/><circle cx="22" cy="21" r="7"/></svg>
      <span>Regular<br>Financial<br>Reports</span>
    </li>
    <li class="hex navy" style="left:60px;top:870px">
      <svg viewBox="0 0 32 32" fill="none" stroke="#fff" stroke-width="2"><rect x="6" y="5" width="20" height="8"/><rect x="4" y="13" width="24" height="9"/><path d="M9 22v6h14v-6"/></svg>
      <span>Vantly and<br>Brimfolk<br>Set-Up and<br>Training</span>
    </li>
  </ul>

  <div class="abs badges" aria-hidden="true">
    <div class="badge-shield"></div>
    <div class="badge-round"></div>
    <div class="badge-round dark"></div>
  </div>

  <div class="abs experience">
    <div class="exp-over">WE HAVE OVER</div>
    <div class="exp-num">2<span>0</span></div>
    <div class="exp-tag">Years</div>
    <div class="exp-ind">INDUSTRY</div>
    <div class="exp-exp">EXPERIENCE</div>
  </div>

  <p class="abs about">and, as a small business ourselves, we are able to offer our clients a personal bookkeeping solution tailored to meet the needs of your business.</p>

  <h2 class="abs question">Are you a small business<br>owner, tradie or TRPQ<br>Service Provider<br>struggling to stay on top<br>of <em>your bookkeeping</em> &amp;<br><em>compliance obligations?</em></h2>

  <p class="abs pitch">If so we would love to help you get<br>back on track and take control of your<br>business finances so that you can<br>make informed business decisions<br>and focus on what you do best.</p>

  <div class="abs call">
    <div class="call-label">Call us</div>
    <div class="call-number">
      <svg viewBox="0 0 36 36"><circle cx="18" cy="18" r="17" fill="#0f4661"/><path d="M12 9l4 4-2 3c1 3 3 5 6 6l3-2 4 4-3 3c-7 0-15-8-15-15z" fill="#fff"/></svg>
      0400 123 456
    </div>
  </div>

  <div class="abs web">www.evenkeelfinancialservices.com.au</div>

</main>
</body>
</html>
```